wardrobe/costume stylist needs good business card for own business

Hi:)

I'm wanting a business card for my company. I am a freelance stylist.

I do wardrobe/costume stylist to TV commercials; Films; Fashion and Lifestyle shoots.

I'd like a design based around my name Rosalind Parfrey written nicely, maybe a colour? Up to you?!

I've attached a couple of images of business cards I like
.... be creative and have fun!

Thank you :)

Reason: I was trying to get my new business card ready for before I headed overseas Friday morning but I don't think that was realistic so I'd like to extend the deadline to give time to the project. Thank you

Hi designers:) Thank you for all your designs, I've extended the deadline until Sunday, so there's a bit more time. I've attached 3 pictures of business cards which I quite like, please take a look to see if it can be of help in your process. I like the pale plain or patterned background with dark font and the dark plain or patterned background with the pale font the motifs the feminine fonts the plain fonts I like the idea of playing with a circle or some shape on one side of the card with my name or initials as in the picture I have on my post could you play around with this idea a bit please? Thank you all for the work you've done :) Rosa

Hi I am working overseas til Saturday night sorry for no feedback until I teturn Thanks :) Rosa

Hi designers, Thank you all so much for submitting your designs, I really appreciate your input into my project :) I'm sorry I didn't get to respond to some comments, and give feedback. I didn't back from being away until later than I expected, and the deadline had passed then, so apologies. Thanks to you all again for all your really good designs :) Rosa

Target Market(s)

I am a freelance stylist my target audience is producers, production companies, photographers, directors...

Industry/Entity Type

Business

Requirements
Must have
• Rosalind Parfrey
Stylist or Wardrobe Stylist

email rosaparfrey@mailbox-example.co.nz
Mobile 0218467193

(Don't have to use the words 'email' and 'mobile')
Nice to have
• Would like it to be double sided
Like B & W
Like pale colour background with dark font or white font
Like dark colour background with pale font
Should not have
• I would prefer it not to incorporate pictures

```html
<!DOCTYPE html>
<html lang="en">
<head>
<meta charset="utf-8">
<title>Rosalind Parfrey – Wardrobe Stylist business card</title>
<link rel="stylesheet" href="https://fonts.googleapis.com/css2?family=Yellowtail&family=Arimo:wght@400;700&display=swap">
<style>
  :root {
    --magenta: #e5097f;
    --sky: #19aeea;
    --ink: #262626;
    --paper: #ffffff;
    --backdrop: #ececec;
    --script: "Yellowtail", cursive;
    --sans: "Arimo", Arial, sans-serif;
  }
  * { box-sizing: border-box; margin: 0; padding: 0; }
  html, body { width: 1200px; height: 533px; overflow: hidden; }
  body {
    background: var(--backdrop);
    display: flex;
    align-items: center;
    justify-content: center;
    gap: 40px;
    font-family: var(--sans);
  }
  .card {
    position: relative;
    width: 540px;
    height: 302px;
    background: var(--paper);
    overflow: hidden;
    box-shadow: 0 2px 8px rgba(0,0,0,0.12);
  }

  /* Front */
  .front__header {
    position: absolute; left: 0; top: 0; width: 100%; height: 177px;
    background: var(--magenta);
    display: flex; align-items: center; justify-content: center; gap: 14px;
    padding-top: 4px;
  }
  .brand-dot {
    width: 42px; height: 42px; border-radius: 50%;
    background: var(--ink);
    flex: none;
  }
  .front__name {
    font-family: var(--script);
    color: var(--paper);
    font-size: 50px;
    line-height: 1;
  }
  .front__band {
    position: absolute; left: 0; top: 177px; width: 100%; height: 28px;
    background: var(--sky);
    display: flex; align-items: center; gap: 8px;
    padding-left: 22px;
  }
  .band__name {
    font-weight: 700; font-size: 15px; color: var(--ink);
    letter-spacing: -0.2px;
  }
  .band__role {
    font-weight: 700; font-size: 8px; color: var(--ink);
    letter-spacing: 0.3px; padding-top: 3px;
  }
  .contact {
    position: absolute; left: 22px; top: 217px;
    list-style: none;
    display: flex; flex-direction: column; gap: 12px;
  }
  .contact__item {
    display: flex; align-items: center; gap: 10px;
    font-size: 14px; color: var(--ink);
  }
  .contact__icon { width: 22px; height: 22px; flex: none; }

  /* Back */
  .back__field {
    position: absolute; left: 0; top: 0; width: 472px; height: 100%;
    background: var(--sky);
    display: flex; align-items: center; justify-content: center;
  }
  .back__rule {
    position: absolute; left: 472px; top: 0; width: 6px; height: 100%;
    background: var(--magenta);
  }
  .back__mark {
    width: 112px; height: 112px; border-radius: 50%;
    background: var(--ink);
    display: flex; align-items: center; justify-content: center;
    text-align: center;
    color: var(--paper);
    font-weight: 700; font-size: 11px; line-height: 1.35; letter-spacing: 0.6px;
  }
  .back__name {
    position: absolute; left: 509px; top: 151px;
    transform: translate(-50%, -50%) rotate(90deg);
    font-family: var(--script);
    font-size: 40px; line-height: 1;
    color: var(--ink);
    white-space: nowrap;
  }
</style>
</head>
<body>

  <section class="card front" aria-label="Card front">
    <header class="front__header">
      <span class="brand-dot" aria-hidden="true"></span>
      <h1 class="front__name">Rosalind Parfrey</h1>
    </header>
    <div class="front__band">
      <span class="band__name">ROSALIND PARFREY</span>
      <span class="band__role">WARDROBE STYLIST</span>
    </div>
    <ul class="contact">
      <li class="contact__item">
        <svg class="contact__icon" viewBox="0 0 22 22" aria-hidden="true">
          <rect width="22" height="22" fill="var(--magenta)"/>
          <rect x="4" y="6.5" width="14" height="9.5" fill="none" stroke="#fff" stroke-width="1.6"/>
          <polyline points="4,6.5 11,12 18,6.5" fill="none" stroke="#fff" stroke-width="1.6"/>
        </svg>
        <span>rosaparfrey@mailbox-example.co.nz</span>
      </li>
      <li class="contact__item">
        <svg class="contact__icon" viewBox="0 0 22 22" aria-hidden="true">
          <rect width="22" height="22" fill="var(--magenta)"/>
          <rect x="7" y="3.5" width="8" height="15" rx="1.2" fill="none" stroke="#fff" stroke-width="1.6"/>
          <line x1="9.5" y1="15.5" x2="12.5" y2="15.5" stroke="#fff" stroke-width="1.6"/>
        </svg>
        <span>0218467193</span>
      </li>
    </ul>
  </section>

  <section class="card back" aria-label="Card back">
    <div class="back__field">
      <div class="back__mark">ROSALIND<br>PARFREY</div>
    </div>
    <div class="back__rule"></div>
    <p class="back__name">Rosalind Parfrey</p>
  </section>

</body>
</html>
```